Pell Dental Care Small Tote Bag

Pell Dental Care needs an advertisement design for a BrightKart Small Tote Bag. See website "www.pelldental-example.com." See uploaded files for small tote bag design template, color scheme, logos, and photo image of Dr. Pell. Designer may crop photo as necessary.

Target Market(s)

Target market is Adults ages 35 to 80.

Industry/Entity Type

Dental

Font styles to use
Sans Serif

```html
<!DOCTYPE html>
<html lang="en">
<head>
<meta charset="utf-8">
<title>Pell Dental Care – Small Tote Bag Advertisement</title>
<link rel="stylesheet" href="https://fonts.googleapis.com/css2?family=Lato:wght@400;700&display=swap">
<style>
  :root {
    --page-bg: #e6e6e6;
    --fabric: #f7f6f1;
    --brand-green: #2f5e50;
    --soft-green: #6f9c8c;
    --text-dark: #2a2a2a;
    --warm-brown: #7d6b5e;
    --photo-light: #e9eaec;
    --photo-mid: #c9ccd2;
    --line-light: #c8d8d1;
  }
  * { box-sizing: border-box; margin: 0; padding: 0; }
  html, body { width: 1200px; height: 1000px; overflow: hidden; }
  body {
    background: var(--page-bg);
    font-family: "Lato", Arial, sans-serif;
    position: relative;
  }
  .artboard {
    position: absolute;
    left: 120px; top: 60px;
    width: 960px; height: 880px;
    background: var(--fabric);
  }
  .brand-name {
    position: absolute;
    left: 40px; top: 110px;
    font-size: 56px; font-weight: 400;
    color: var(--brand-green);
    line-height: 1;
    white-space: nowrap;
  }
  .brand-name::before {
    content: ""; display: inline-block;
    width: 22px; height: 22px; border-radius: 50%;
    background: var(--soft-green);
    margin-right: 14px; vertical-align: middle;
  }
  .services {
    position: absolute;
    left: 60px; top: 215px;
    list-style: none;
    font-size: 32px; color: var(--text-dark);
    line-height: 46px;
  }
  .services li::before { content: "\2022"; margin-right: 12px; }
  .doctor-photo {
    position: absolute;
    left: 540px; top: 20px;
    width: 380px; height: 490px;
    background: linear-gradient(180deg, var(--photo-light) 0%, var(--photo-mid) 100%);
    border-radius: 190px 190px 0 0;
  }
  .doctor-caption {
    position: absolute;
    left: 540px; top: 440px; width: 380px;
    text-align: center;
    font-size: 26px; color: var(--text-dark);
  }
  .tagline {
    position: absolute;
    left: 0; top: 545px; width: 400px;
    text-align: center;
    font-size: 32px; line-height: 46px;
    color: var(--warm-brown);
  }
  .tagline .highlight { color: var(--soft-green); font-weight: 700; }
  .call-block {
    position: absolute;
    left: 420px; top: 555px;
    display: flex; align-items: center; gap: 16px;
  }
  .call-text { color: var(--text-dark); line-height: 1.15; white-space: nowrap; }
  .call-label { font-size: 40px; }
  .call-number { font-size: 50px; font-weight: 700; }
  .web-band {
    position: absolute;
    left: 40px; top: 720px;
    width: 880px; height: 120px;
  }
  .web-band svg { position: absolute; inset: 0; }
  .web-address {
    position: absolute; left: 0; right: 0; top: 34px;
    text-align: center;
    font-size: 52px; color: #fff;
  }
  .web-address strong { font-weight: 700; }
</style>
</head>
<body>
  <main class="artboard">
    <div class="brand-name">Pell Dental Care</div>

    <ul class="services">
      <li>General Dentistry</li>
      <li>Cosmetic Dentistry</li>
      <li>Beautiful Dentures</li>
      <li>Sedation Dentistry</li>
    </ul>

    <div class="doctor-photo" role="img" aria-label="Portrait photo of Dr. Owen Pell in a white coat with arms crossed"></div>
    <div class="doctor-caption">Dr. Owen Pell</div>

    <p class="tagline">Life-Changing<br><span class="highlight">Family Dental Care</span><br>In Cedar Hollow</p>

    <div class="call-block">
      <svg class="phone-icon" width="54" height="100" viewBox="0 0 54 100" aria-hidden="true">
        <rect x="2" y="2" width="50" height="96" rx="8" fill="var(--brand-green)"/>
        <rect x="9" y="12" width="36" height="32" rx="3" fill="var(--soft-green)"/>
        <g fill="var(--fabric)">
          <rect x="10" y="54" width="9" height="6"/><rect x="23" y="54" width="9" height="6"/><rect x="36" y="54" width="9" height="6"/>
          <rect x="10" y="65" width="9" height="6"/><rect x="23" y="65" width="9" height="6"/><rect x="36" y="65" width="9" height="6"/>
          <rect x="10" y="76" width="9" height="6"/><rect x="23" y="76" width="9" height="6"/><rect x="36" y="76" width="9" height="6"/>
        </g>
      </svg>
      <div class="call-text">
        <div class="call-label">Call Us Today!</div>
        <div class="call-number">(555) 013-2740</div>
      </div>
    </div>

    <div class="web-band">
      <svg width="880" height="120" viewBox="0 0 880 120" aria-hidden="true">
        <path d="M0 14 Q440 -6 880 14 L880 120 L0 120 Z" fill="var(--brand-green)"/>
        <path d="M0 8 Q440 -12 880 8" fill="none" stroke="var(--line-light)" stroke-width="3"/>
      </svg>
      <div class="web-address">www.<strong>pelldental-example</strong>.com</div>
    </div>
  </main>
</body>
</html>
```